Brookmere Osteopathy flyer

I want a clean clear DL flyer (but also want an A4 poster) promoting a new Osteopathic business in a semi rural area in Tasmania (Australia).
It can have pictures like the examples attached to show people what Osteopathy is (its like Chiropractic and physiotherapy).
I am the sole practioner and am male, so any pictures would be best to be a white male if possible.
I've attached some wording, you can use all, or none of it
I don't have a phone number for the business yet
info@brookmereosteopathy.example
www.brookmereosteopathy.example
Target Market(s)
Australians, from tradies, professionals, babies to retired people
Industry/Entity Type
Health
Look and feel

```html
<!DOCTYPE html>
<html lang="en">
<head>
<meta charset="utf-8">
<title>Brookmere Osteopathy – DL flyer and A4 poster</title>
<link rel="stylesheet" href="https://fonts.googleapis.com/css2?family=Nunito:wght@800;900&family=Open+Sans:wght@400;600&display=swap">
<style>
  :root {
    --navy-deep: #04062e;
    --navy: #0b1a6e;
    --royal: #2446b8;
    --sky: #1b7fd4;
    --accent: #0a80cf;
    --ice: #a9e4ff;
    --ink: #1e1e22;
    --paper: #ffffff;
    --stage: #ffffff;
  }
  * { margin: 0; padding: 0; box-sizing: border-box; }
  html, body { width: 1200px; height: 848px; overflow: hidden; background: var(--stage); }
  body { position: relative; font-family: "Open Sans", sans-serif; color: var(--ink); }

  .flyer {
    position: absolute; top: 48px; height: 750px; background: var(--paper);
    overflow: hidden; box-shadow: 0 0 3px rgba(0,0,0,.25);
  }
  .flyer--dl { left: 146px; width: 355px; }
  .flyer--a4 { left: 526px; width: 531px; }
  .flyer__art { position: absolute; inset: 0; width: 100%; height: 100%; }

  .brand { position: absolute; display: flex; align-items: center; gap: 6px; color: var(--paper);
    font-family: "Open Sans", sans-serif; font-weight: 600; line-height: 1.15; }
  .brand__dot { border: 2px solid var(--paper); border-radius: 50%; flex: none; }

  .headline { position: absolute; font-family: "Nunito", sans-serif; font-weight: 900;
    color: var(--paper); line-height: 1; }
  .headline__accent { color: var(--ice); }

  .title { position: absolute; font-family: "Nunito", sans-serif; font-weight: 900;
    color: var(--accent); line-height: 1.1; }
  .copy { position: absolute; line-height: 1.25; }

  .rule { position: absolute; background: var(--accent); }

  .conditions { position: absolute; list-style: none; border-left: 1.5px solid var(--accent); }
  .conditions li { position: relative; padding-left: 6px; }
  .conditions li::before { content: ""; position: absolute; left: -3.5px; top: 50%;
    width: 5px; height: 5px; margin-top: -2.5px; border-radius: 50%; background: var(--accent); }

  .contact { position: absolute; }
  .contact__title { font-family: "Nunito", sans-serif; font-weight: 900; color: var(--accent); }
  .contact__line { display: flex; align-items: center; gap: 5px; white-space: nowrap; }
  .contact__line svg { flex: none; fill: var(--accent); }
  .contact__line--spaced { letter-spacing: 1.6px; }
</style>
</head>
<body>

<!-- DL flyer -->
<section class="flyer flyer--dl">
  <svg class="flyer__art" viewBox="0 0 355 750" aria-hidden="false">
    <defs>
      <linearGradient id="dl-hero" x1="0" y1="0" x2="1" y2="1">
        <stop offset="0" stop-color="#101f80"/>
        <stop offset=".6" stop-color="#06093f"/>
        <stop offset="1" stop-color="#03052a"/>
      </linearGradient>
      <linearGradient id="dl-strip" x1="0" y1="0" x2="1" y2="0">
        <stop offset="0" stop-color="#9ab0d8"/>
        <stop offset=".5" stop-color="#5a7fd0"/>
        <stop offset="1" stop-color="#2747b0"/>
      </linearGradient>
      <linearGradient id="dl-tri" x1="0" y1="1" x2="1" y2="0">
        <stop offset="0" stop-color="#1c8be0"/>
        <stop offset="1" stop-color="#2a44bd"/>
      </linearGradient>
    </defs>
    <polygon points="0,0 355,0 355,346 0,219" fill="url(#dl-hero)" role="img" aria-label="Blue x-ray style image of a human spine and shoulders"/>
    <polygon points="172,43 355,43 355,346 172,280" fill="#e6eaf2" role="img" aria-label="Portrait of the practitioner in a white coat, arms folded"/>
    <polygon points="0,229 355,354 355,478 0,351" fill="url(#dl-strip)" role="img" aria-label="Photos of osteopathic hands-on treatment for adults and a newborn"/>
    <polygon points="261,312 355,262 355,348" fill="url(#dl-tri)"/>
  </svg>

  <div class="brand" style="left:24px; top:80px; font-size:10px;">
    <span class="brand__dot" style="width:22px; height:22px;"></span>
    <span>Brookmere<br>Osteopathy</span>
  </div>

  <h1 class="headline" style="left:41px; top:138px; font-size:20px; line-height:20.5px;">
    This isn't just<br>treatment.<br>This is your<br><span class="headline__accent">life again.</span>
  </h1>

  <h2 class="title" style="left:25px; top:390px; font-size:23px; line-height:27px;">Who Do<br>We Treat?</h2>
  <p class="copy" style="left:25px; top:444px; width:300px; font-size:13.4px; line-height:16.7px;">
    From active tradies and busy professionals to newborns and retirees — everyone is welcome. Treatments are always adjusted to suit your body, your lifestyle, and your goals.
  </p>

  <div class="rule" style="left:16px; top:531px; width:323px; height:1.5px;"></div>

  <h3 class="title" style="left:25px; top:541px; font-size:11.8px;">What is Osteopathy?</h3>
  <p class="copy" style="left:25px; top:556px; width:140px; font-size:12.4px; line-height:15.2px;">
    Gentle treatment to reduce pain, improve mobility and help your body heal naturally using massage, joint movement &amp; stretching.
  </p>

  <h3 class="title" style="left:188px; top:541px; font-size:14px; line-height:16.5px;">Osteopathy can<br>assist with:</h3>
  <ul class="conditions" style="left:187px; top:578px; font-size:12.4px; line-height:15.7px;">
    <li>Back &amp; neck pain</li>
    <li>Sciatica &amp; disc issues</li>
    <li>Headaches</li>
    <li>Pregnancy discomfort</li>
    <li>Joint &amp; muscle problems</li>
  </ul>

  <div class="rule" style="left:16px; top:674px; width:323px; height:1.5px;"></div>

  <div class="contact" style="left:45px; top:680px; font-size:11.4px; line-height:15.2px;">
    <div class="contact__title" style="font-size:13px; line-height:17px;">Contact Us:</div>
    <div class="contact__line contact__line--spaced" style="letter-spacing:1.1px;">
      <svg width="9" height="7" viewBox="0 0 9 7"><path d="M0 0h9v7H0z M0 0l4.5 3.8L9 0" fill="var(--accent)" stroke="#fff" stroke-width=".7"/></svg>
      info@brookmereosteopathy.example
    </div>
    <div class="contact__line contact__line--spaced" style="letter-spacing:1.1px;">
      <svg width="9" height="9" viewBox="0 0 10 10"><circle cx="5" cy="5" r="4.5"/><path d="M.5 5h9M5 .5v9" stroke="#fff" stroke-width=".8"/></svg>
      www.brookmereosteopathy.example
    </div>
    <div class="contact__line" style="letter-spacing:.4px;">
      <svg width="8" height="10" viewBox="0 0 8 10"><path d="M4 0a4 4 0 0 1 4 4c0 3-4 6-4 6S0 7 0 4a4 4 0 0 1 4-4z"/><circle cx="4" cy="4" r="1.5" fill="#fff"/></svg>
      Serving Brookmere and surrounding areas
    </div>
  </div>
</section>

<!-- A4 poster -->
<section class="flyer flyer--a4">
  <svg class="flyer__art" viewBox="0 0 531 750">
    <defs>
      <linearGradient id="a4-hero" x1="0" y1="0" x2="1" y2="1">
        <stop offset="0" stop-color="#101f80"/>
        <stop offset=".6" stop-color="#06093f"/>
        <stop offset="1" stop-color="#03052a"/>
      </linearGradient>
      <linearGradient id="a4-strip" x1="0" y1="0" x2="1" y2="0">
        <stop offset="0" stop-color="#9ab0d8"/>
        <stop offset=".5" stop-color="#5a7fd0"/>
        <stop offset="1" stop-color="#2747b0"/>
      </linearGradient>
      <linearGradient id="a4-tri" x1="0" y1="1" x2="1" y2="0">
        <stop offset="0" stop-color="#1c8be0"/>
        <stop offset="1" stop-color="#2a44bd"/>
      </linearGradient>
    </defs>
    <polygon points="0,0 531,0 531,435 0,276" fill="url(#a4-hero)" role="img" aria-label="Blue x-ray style image of a human spine and shoulders"/>
    <polygon points="267,38 524,38 524,433 267,356" fill="#e6eaf2" role="img" aria-label="Portrait of the practitioner in a white coat, arms folded"/>
    <polygon points="0,286 531,440 531,555 0,390" fill="url(#a4-strip)" role="img" aria-label="Photos of osteopathic hands-on treatment for adults and a newborn"/>
    <polygon points="385,385 531,309 531,435" fill="url(#a4-tri)"/>
  </svg>

  <div class="brand" style="left:94px; top:90px; font-size:13px;">
    <span class="brand__dot" style="width:28px; height:28px;"></span>
    <span>Brookmere<br>Osteopathy</span>
  </div>

  <h1 class="headline" style="left:93px; top:165px; font-size:27px; line-height:26.7px;">
    This isn't just<br>treatment.<br>This is your<br><span class="headline__accent">life again.</span>
  </h1>

  <h2 class="title" style="left:37px; top:434px; font-size:21px; line-height:25px;">Who Do<br>We Treat?</h2>
  <p class="copy" style="left:37px; top:484px; width:250px; font-size:12.3px; line-height:15.3px;">
    From active tradies and busy professionals to newborns and retirees — everyone is welcome. Treatments are always adjusted to suit your body, your lifestyle, and your goals.
  </p>

  <div class="rule" style="left:284px; top:516px; width:1.5px; height:128px;"></div>
  <div class="rule" style="left:33px; top:568px; width:251px; height:1.5px;"></div>

  <h3 class="title" style="left:33px; top:576px; font-size:21px;">What is Osteopathy?</h3>
  <p class="copy" style="left:33px; top:603px; width:250px; font-size:11.3px; line-height:14px;">
    Gentle treatment to reduce pain, improve mobility and help your body heal naturally using massage, joint movement &amp; stretching.
  </p>

  <h3 class="title" style="left:299px; top:524px; font-size:14.5px; line-height:17px;">Osteopathy can<br>assist with:</h3>
  <ul class="conditions" style="left:299px; top:560px; font-size:13.3px; line-height:16.2px;">
    <li>Back &amp; neck pain</li>
    <li>Sciatica &amp; disc issues</li>
    <li>Headaches</li>
    <li>Pregnancy discomfort</li>
    <li>Joint &amp; muscle problems</li>
  </ul>

  <div class="rule" style="left:33px; top:659px; width:457px; height:1.5px;"></div>

  <div class="contact" style="left:37px; top:666px; font-size:13px; line-height:15.8px;">
    <div class="contact__title" style="font-size:14.5px; line-height:18px;">Contact Us:</div>
    <div class="contact__line contact__line--spaced" style="letter-spacing:2.2px;">
      <svg width="10" height="8" viewBox="0 0 9 7"><path d="M0 0h9v7H0z M0 0l4.5 3.8L9 0" fill="var(--accent)" stroke="#fff" stroke-width=".7"/></svg>
      info@brookmereosteopathy.example
    </div>
    <div class="contact__line contact__line--spaced" style="letter-spacing:2.2px;">
      <svg width="10" height="10" viewBox="0 0 10 10"><circle cx="5" cy="5" r="4.5"/><path d="M.5 5h9M5 .5v9" stroke="#fff" stroke-width=".8"/></svg>
      www.brookmereosteopathy.example
    </div>
    <div class="contact__line" style="letter-spacing:.5px;">
      <svg width="9" height="11" viewBox="0 0 8 10"><path d="M4 0a4 4 0 0 1 4 4c0 3-4 6-4 6S0 7 0 4a4 4 0 0 1 4-4z"/><circle cx="4" cy="4" r="1.5" fill="#fff"/></svg>
      Serving Brookmere and surrounding areas
    </div>
  </div>
</section>

</body>
</html>
```